Verdano Tiling Solutions, QBCC 4870312, ABN 28459106783, Email verdanotiling@tilebox-mail.com,Mobile 04159326

Verdano Tiling Solutions, is the name of my wall and floor tiling company and the details above are needed on the business card. Im open to see what people come up with i really have no colour requirements or other design specs as long as its not too plain.

```html
<!DOCTYPE html>
<html lang="en">
<head>
<meta charset="utf-8">
<title>Verdano Tiling Solutions — Business Card</title>
<link rel="stylesheet" href="https://fonts.googleapis.com/css2?family=Open+Sans:wght@300;400;600&display=swap">
<style>
  :root {
    --page: #e9e6e1;
    --paper: #ffffff;
    --charcoal: #2b2b2b;
    --orange: #e56f16;
    --orange-deep: #c85a0c;
    --red: #e3232e;
    --red-deep: #c3141f;
    --ink: #3a3a3a;
    --muted: #6b6b6b;
  }
  * { box-sizing: border-box; margin: 0; padding: 0; }
  html, body { width: 1072px; height: 1200px; overflow: hidden; }
  body {
    background: var(--page);
    font-family: "Open Sans", Arial, sans-serif;
    display: flex;
    flex-direction: column;
    align-items: center;
    justify-content: center;
    gap: 70px;
  }
  .card {
    position: relative;
    width: 900px;
    height: 514px;
    background: var(--paper);
    overflow: hidden;
    box-shadow: 0 10px 30px rgba(0,0,0,.18);
  }

  /* Front */
  .front .band-orange {
    position: absolute; left: 0; right: 0; top: 300px; height: 34px;
    background: linear-gradient(90deg, var(--orange-deep), var(--orange));
  }
  .front .field-dark {
    position: absolute; left: 0; right: 0; top: 334px; bottom: 0;
    background: var(--charcoal);
  }
  .front .corner-dark {
    position: absolute; right: 0; top: 234px; width: 240px; height: 66px;
    background: var(--charcoal);
  }
  .front .panel-red {
    position: absolute; left: 70px; top: 360px; width: 430px; height: 154px;
    background: radial-gradient(circle at 50% 30%, var(--red), var(--red-deep));
    clip-path: polygon(0 0, 100% 0, 88% 100%, 0 100%);
  }
  .brand-name {
    font-weight: 400; color: var(--ink); letter-spacing: .5px; white-space: nowrap;
  }
  .front .brand-name {
    position: absolute; left: 0; right: 0; top: 122px;
    text-align: center; font-size: 30px;
  }

  /* Back */
  .back .strip-orange-top {
    position: absolute; left: 520px; right: 0; top: 0; height: 40px;
    background: linear-gradient(90deg, var(--orange-deep), var(--orange));
  }
  .back .band-orange {
    position: absolute; left: 520px; top: 0; bottom: 0; width: 34px;
    background: linear-gradient(180deg, var(--orange), var(--orange-deep));
  }
  .back .field-dark {
    position: absolute; left: 554px; right: 0; top: 40px; bottom: 0;
    background: var(--charcoal);
  }
  .back .name-box {
    position: absolute; left: 610px; top: 220px; width: 290px; height: 110px;
    background: radial-gradient(circle at 40% 40%, var(--red), var(--red-deep));
    color: #fff; padding: 26px 0 0 34px;
  }
  .name-box .person {
    font-size: 26px; font-weight: 400; letter-spacing: 1.5px; text-transform: uppercase;
  }
  .name-box .role {
    font-size: 14px; font-weight: 300; margin-top: 4px; letter-spacing: .5px;
  }
  .back .brand-name {
    position: absolute; left: 54px; top: 110px; font-size: 30px;
  }
  .contact-list {
    position: absolute; left: 54px; top: 250px; list-style: none;
    display: flex; flex-direction: column; gap: 16px;
  }
  .contact-list li {
    display: flex; align-items: center; gap: 14px;
    font-size: 16px; color: var(--muted); font-weight: 400;
  }
  .contact-list svg { width: 18px; height: 18px; flex: none; }
</style>
</head>
<body>

  <section class="card front" aria-label="Card front">
    <div class="corner-dark"></div>
    <div class="band-orange"></div>
    <div class="field-dark"></div>
    <div class="panel-red"></div>
    <p class="brand-name">Verdano Tiling Solutions</p>
  </section>

  <section class="card back" aria-label="Card back">
    <div class="strip-orange-top"></div>
    <div class="band-orange"></div>
    <div class="field-dark"></div>
    <div class="name-box">
      <p class="person">Daniel Reyes</p>
      <p class="role">General Manager</p>
    </div>

    <p class="brand-name">Verdano Tiling Solutions</p>

    <ul class="contact-list">
      <li>
        <svg viewBox="0 0 24 24" aria-hidden="true"><path fill="#e3232e" d="M6.6 10.8a15 15 0 0 0 6.6 6.6l2.2-2.2c.3-.3.7-.4 1-.2 1.1.4 2.3.6 3.6.6.6 0 1 .4 1 1V20c0 .6-.4 1-1 1A17 17 0 0 1 3 4c0-.6.4-1 1-1h3.5c.6 0 1 .4 1 1 0 1.3.2 2.5.6 3.6.1.3 0 .7-.2 1z"/></svg>
        Mobile 04159326
      </li>
      <li>
        <svg viewBox="0 0 24 24" aria-hidden="true"><rect x="2" y="5" width="20" height="14" rx="2" fill="#e3232e"/><path d="M3 6l9 7 9-7" stroke="#fff" stroke-width="1.6" fill="none"/></svg>
        verdanotiling@tilebox-mail.com
      </li>
      <li>
        <svg viewBox="0 0 24 24" aria-hidden="true"><circle cx="12" cy="12" r="9" fill="#e3232e"/><path d="M8 12.5l3 3 5-6" stroke="#fff" stroke-width="2" fill="none"/></svg>
        QBCC 4870312
      </li>
      <li>
        <svg viewBox="0 0 24 24" aria-hidden="true"><path fill="#e3232e" d="M12 2a7 7 0 0 0-7 7c0 5 7 13 7 13s7-8 7-13a7 7 0 0 0-7-7zm0 9.5A2.5 2.5 0 1 1 12 6.5a2.5 2.5 0 0 1 0 5z"/></svg>
        ABN 28459106783
      </li>
    </ul>
  </section>

</body>
</html>
```